Silvermoor Property Development Co.

We need a logo and business card design for a Hong Kong based real estate company, PLX Land. We are want the brand to reflect the owners forward thinking, creative, and trend setting projects, while also reflecting a sense of security and strength. We invest in industrial properties which we convert to co-living or co-working spaces. PLX stands for Greater Bay Area which is the region around southern China including HK, Macau, and 9 other Chinese cities...made up of approx. 68 million people. There are massive infrastructure projects including the bridge to Macau and high-speed rail to SZ and the bridge connecting SZ and Zhongshan.

Target Market(s)

Chinese and western retail investors, as well as institutional investors

Industry/Entity Type

Real Estate Development

Contact Information for Business Card

Dale Whitford
CEO
dale@plxland-example.com
M + 852 9581 4062
F + 852 3864 2217
Suite 2207, The Halvern, 41 Tremont Rd., Central, Hong Kong

Logo Text

plx land (company name) lifestyle property development (underneath)

Colors

Designer to choose colors to be used in the design.

Requirements
Must have
• Details listed above. One side should include the logo and company name...plx land in modern, hip styling with "lifestyle property development"
Nice to have
• Could be a Black card, with metallic purple "plx" and white "land"...but open great design ideas
Should not have
• boring and traditional layout

```html
<!DOCTYPE html>
<html lang="en">
<head>
<meta charset="utf-8">
<title>PLX Land – Business Card</title>
<link rel="stylesheet" href="https://fonts.googleapis.com/css2?family=Montserrat:wght@600;700&family=Open+Sans:wght@400;600&family=Arimo:wght@400;700&display=swap">
<style>
  :root {
    --backdrop: #363636;
    --card-top: #2a2a2a;
    --card-bottom: #232323;
    --card-back-top: #313131;
    --purple: #7a1fa8;
    --white: #ffffff;
    --muted: #cfcfcf;
  }
  * { margin: 0; padding: 0; box-sizing: border-box; }
  html, body {
    width: 1042px; height: 1200px; overflow: hidden;
    background: var(--backdrop);
  }
  .canvas { position: relative; width: 1042px; height: 1200px; }
  .card {
    position: absolute; left: 170px; width: 714px; height: 420px;
    border-radius: 22px;
    background: linear-gradient(180deg, var(--card-top), var(--card-bottom));
  }
  .card--front { top: 126px; }
  .card--back {
    top: 616px;
    background: radial-gradient(ellipse at 50% 20%, var(--card-back-top), var(--card-bottom) 75%);
  }
  .wordmark {
    position: absolute; left: 0; right: 0; text-align: center;
    font-family: "Montserrat", sans-serif; font-weight: 700;
  }
  .wordmark--symbol { top: 80px; font-size: 118px; line-height: 1; color: var(--purple); letter-spacing: 2px; }
  .wordmark--name { top: 228px; font-size: 56px; line-height: 1; color: var(--white); }
  .tagline {
    position: absolute; left: 0; right: 0; top: 296px; text-align: center;
    font-family: "Montserrat", sans-serif; font-weight: 600; font-size: 14px;
    letter-spacing: 3px; text-transform: uppercase; color: var(--muted);
  }
  .address {
    position: absolute; left: 0; right: 0; top: 358px; text-align: center;
    font-family: "Open Sans", sans-serif; font-weight: 600; font-size: 18px; color: var(--white);
  }
  .back-mark {
    position: absolute; left: 112px; top: 160px; width: 194px;
    text-align: center; font-family: "Montserrat", sans-serif; font-weight: 700;
    font-size: 90px; line-height: 1; color: var(--purple);
  }
  .divider {
    position: absolute; left: 329px; top: 128px; width: 3px; height: 182px; background: var(--purple);
  }
  .person { position: absolute; left: 360px; top: 122px; }
  .person__name {
    font-family: "Arimo", sans-serif; font-weight: 400; font-size: 36px; line-height: 1;
    color: var(--white); white-space: nowrap;
  }
  .person__name b { color: var(--purple); font-weight: 700; }
  .person__role {
    display: flex; align-items: center; gap: 10px; margin-top: 6px;
    font-family: "Arimo", sans-serif; font-weight: 700; font-size: 24px; letter-spacing: 2px; color: var(--white);
  }
  .person__role::after { content: ""; width: 150px; height: 3px; background: var(--purple); }
  .contacts { position: absolute; left: 360px; top: 220px; list-style: none; }
  .contacts li {
    display: flex; align-items: center; gap: 14px; height: 31px;
    font-family: "Open Sans", sans-serif; font-size: 22px; color: var(--white);
  }
  .contacts svg { width: 16px; height: 16px; fill: var(--purple); flex: none; }
</style>
</head>
<body>
<main class="canvas">
  <section class="card card--front" aria-label="Card front">
    <div class="wordmark wordmark--symbol">plx</div>
    <div class="wordmark wordmark--name">PLX Land</div>
    <p class="tagline">lifestyle property development</p>
    <p class="address">Suite 2207, The Halvern, 41 Tremont Rd., Central, Hong Kong</p>
  </section>

  <section class="card card--back" aria-label="Card back">
    <div class="back-mark">plx</div>
    <div class="divider"></div>
    <div class="person">
      <h1 class="person__name"><b>DALE</b> WHITFORD</h1>
      <p class="person__role">CEO</p>
    </div>
    <ul class="contacts">
      <li>
        <svg viewBox="0 0 24 24" aria-hidden="true"><path d="M6.6 10.8a15.1 15.1 0 0 0 6.6 6.6l2.2-2.2a1 1 0 0 1 1-.25 11.4 11.4 0 0 0 3.6.57 1 1 0 0 1 1 1V20a1 1 0 0 1-1 1A17 17 0 0 1 3 4a1 1 0 0 1 1-1h3.5a1 1 0 0 1 1 1c0 1.25.2 2.45.57 3.57a1 1 0 0 1-.25 1z"/></svg>
        852 9581 4062
      </li>
      <li>
        <svg viewBox="0 0 24 24" aria-hidden="true"><path d="M6 2h12v5H6zM3 8h18a2 2 0 0 1 2 2v7h-4v5H5v-5H1v-7a2 2 0 0 1 2-2zm4 8v4h10v-4z"/></svg>
        852 3864 2217
      </li>
      <li>
        <svg viewBox="0 0 24 24" aria-hidden="true"><path d="M2 5h20v14H2zm2 2v.5l8 5.5 8-5.5V7l-8 5.5z"/></svg>
        dale@plxland-example.com
      </li>
    </ul>
  </section>
</main>
</body>
</html>
```